Business card design for my company.
I would like the card's background colour to be black. You can also see our web site to get an idea of our brand. https://www.tmwhomecrafting.com.au/
- Name
- Email

```html
<!DOCTYPE html>
<html lang="en">
<head>
<meta charset="UTF-8">
<title>TMW Home Crafting – Business Card</title>
<link href="https://fonts.googleapis.com/css2?family=Montserrat:wght@400;500;700;800&display=swap" rel="stylesheet">
<style>
  :root {
    --canvas: #2b2b2b;
    --card: #050505;
    --green: #12994a;
    --white: #ffffff;
    --muted: #e6e6e6;
  }
  * { box-sizing: border-box; margin: 0; padding: 0; }
  html, body {
    width: 1200px; height: 875px; overflow: hidden;
    background: var(--canvas);
    font-family: "Montserrat", Arial, sans-serif;
  }
  .canvas {
    width: 1200px; height: 875px;
    display: flex; align-items: center; justify-content: center; gap: 40px;
  }
  .card {
    width: 540px; height: 310px;
    background: var(--card);
    border-radius: 16px;
    position: relative;
    overflow: hidden;
  }
  /* Front */
  .card--front { display: flex; align-items: center; justify-content: center; }
  .brand { display: flex; align-items: center; gap: 14px; }
  .brand__mark { width: 22px; height: 22px; background: var(--green); }
  .brand__name {
    color: var(--white); font-weight: 800; font-size: 30px;
    letter-spacing: 2px; text-transform: uppercase;
  }
  /* Back */
  .card--back { display: flex; align-items: center; padding: 0 40px; }
  .card--back .brand { gap: 10px; width: 210px; }
  .card--back .brand__mark { width: 14px; height: 14px; flex: none; }
  .card--back .brand__name { font-size: 17px; letter-spacing: 1.2px; line-height: 1.25; }
  .divider { width: 2px; height: 150px; background: var(--green); margin: 0 28px 0 10px; flex: none; }
  .contact__name { font-size: 24px; font-weight: 800; color: var(--white); }
  .contact__name .first { color: var(--green); }
  .contact__title { font-size: 12.5px; color: var(--muted); margin-top: 2px; margin-bottom: 16px; }
  .contact__list { list-style: none; }
  .contact__item {
    display: flex; align-items: center; gap: 10px;
    font-size: 12.5px; color: var(--muted); margin-bottom: 7px;
  }
  .contact__item svg { width: 14px; height: 14px; flex: none; fill: var(--green); }
</style>
</head>
<body>
<main class="canvas">
  <section class="card card--front">
    <div class="brand">
      <span class="brand__mark"></span>
      <span class="brand__name">TMW Home Crafting</span>
    </div>
  </section>

  <section class="card card--back">
    <div class="brand">
      <span class="brand__mark"></span>
      <span class="brand__name">TMW Home<br>Crafting</span>
    </div>
    <div class="divider"></div>
    <div class="contact">
      <h1 class="contact__name"><span class="first">Liam</span> Carter</h1>
      <p class="contact__title">Managing Director</p>
      <ul class="contact__list">
        <li class="contact__item">
          <svg viewBox="0 0 24 24" aria-hidden="true"><path d="M6.6 10.8a15.1 15.1 0 0 0 6.6 6.6l2.2-2.2a1 1 0 0 1 1-.25 11.4 11.4 0 0 0 3.6.57 1 1 0 0 1 1 1V20a1 1 0 0 1-1 1A17 17 0 0 1 3 4a1 1 0 0 1 1-1h3.5a1 1 0 0 1 1 1c0 1.25.2 2.45.57 3.57a1 1 0 0 1-.25 1z"/></svg>
          (08) 9470 2263
        </li>
        <li class="contact__item">
          <svg viewBox="0 0 24 24" aria-hidden="true"><path d="M2 5h20v14H2z M2 5l10 8 10-8" fill="none" stroke="#12994a" stroke-width="2"/></svg>
          info@tmwhomecrafting.com.au
        </li>
        <li class="contact__item">
          <svg viewBox="0 0 24 24" aria-hidden="true"><circle cx="12" cy="12" r="9" fill="none" stroke="#12994a" stroke-width="2"/><path d="M3 12h18M12 3c3 3 3 15 0 18M12 3c-3 3-3 15 0 18" fill="none" stroke="#12994a" stroke-width="1.6"/></svg>
          www.tmwhomecrafting.com.au
        </li>
      </ul>
    </div>
  </section>
</main>
</body>
</html>
```